Homepage mockup for RoutineVerdict.com

I would like a homepage mockup of routineverdict.com.

Basically what the site does, is it allows a person to upload a video of a gymnastics routine and our certified judges will judge the routine providing a score, as well as provide a critique and feedback as to why they gave you that score. Many times people don't know why they got the score they did at a gymnastics competition, so this site aims to provide reasoning behind it.

I have started to design the homepage myself (see attached), and like it, but I'd like a professional to finish the layout, or even come up with something really wow and original. I like clean, typically simple design.

THIS IS AN OLD VERSION OF THE SITE (http://esite.kelpradia.com/) This should only be used so you can get an idea of what the site is about. I DO NOT want the new site to look like this, but the basic concept and content remains the same.

DESIGNER FILES CAN BE DOWNLOADED HERE (http://kelpradia.com/files.aspx)

Target Market(s)

Gymnastic type people, parents of gymnasts, coaches, etc.

Industry/Entity Type

It Professional

Requirements
Must have
• -Routine verdict logo (provided)
-Not required, but I have attached the main photo I used in my mockup (AI File)
*A step by step graphic(s) depicting the process for a user. A How it works sort of explanation. Should be eye catching, not just text.

-Step 1: Videotape your gymnastic routine.
-Step 2: Create an account and share us your video.
-Step 3: Our certified judges will score and critique your routine, fully explaining the reasons behind their score.

```html
<!DOCTYPE html>
<html lang="en">
<head>
<meta charset="utf-8">
<title>Routine verdict – Your personal gymnastic judge</title>
<link rel="stylesheet" href="https://fonts.googleapis.com/css2?family=Roboto+Condensed:wght@400;700&family=PT+Sans:wght@400;700&display=swap">
<style>
:root{
  --red:#b8161d;
  --red-dark:#9c1218;
  --red-bright:#e02424;
  --blue:#1a6aa6;
  --blue-btn:#1d87d6;
  --orange:#f39a1c;
  --ink:#1a1a1a;
  --grey-text:#666;
  --footer:#555555;
  --footer-line:#7a7a7a;
}
*{margin:0;padding:0;box-sizing:border-box}
html,body{width:1200px;height:1090px;overflow:hidden;background:#fff}
body{font-family:"PT Sans",sans-serif;color:var(--ink);position:relative}
.cond{font-family:"Roboto Condensed",sans-serif}

/* header */
.site-header{position:absolute;left:0;top:0;width:1200px;height:105px;background:linear-gradient(#fafafa,#ececec);box-shadow:0 2px 6px rgba(0,0,0,.12);z-index:3}
.brand{position:absolute;left:173px;top:34px;display:flex;align-items:center;gap:8px}
.brand-mark{width:26px;height:26px;background:var(--blue)}
.brand-name{font-family:"Roboto Condensed",sans-serif;font-weight:700;font-size:32px;color:var(--blue);line-height:1}
.main-nav{position:absolute;left:418px;top:0;height:105px;display:flex;align-items:flex-end}
.main-nav a{font-size:11px;color:var(--red);text-decoration:none;margin-right:45px;line-height:14px;padding-bottom:24px}
.main-nav a.active{background:linear-gradient(var(--red-bright),var(--red));color:#fff;width:55px;height:105px;display:flex;align-items:flex-end;justify-content:center;margin-right:33px}
.login{position:absolute;left:970px;top:65px;width:59px;height:20px;border-radius:3px;background:linear-gradient(#d42a2a,#a51016);color:#fff;font-size:11px;display:flex;align-items:center;justify-content:center}

/* hero */
.hero{position:absolute;left:0;top:105px;width:1200px;height:476px;background:linear-gradient(#f7f7f7 0%,#e3e3e3 55%,#c9c9c9 82%,#efefef 90%,#d8d8d8 100%)}
.hero-copy{position:absolute;left:185px;top:84px;width:340px}
.hero-copy .l1{font-size:27px;color:var(--red);line-height:1.15}
.hero-copy .l2{font-size:31px;color:var(--red);line-height:1.15}
.hero-copy .l3{font-size:23px;color:var(--blue);margin-top:8px;line-height:1.3}
.hero-copy .l4{font-size:23px;color:var(--blue);line-height:1.45}
.hero-copy p{font-family:"PT Sans",sans-serif;font-size:9.5px;line-height:15px;margin-top:10px;color:#111}
.cta{position:absolute;left:191px;top:292px;width:254px;height:69px;border-radius:6px;background:linear-gradient(#c41e25,#a8141a);display:flex;align-items:center;color:#fff}
.cta small{width:115px;text-align:right;font-size:11.5px;line-height:15px;padding-right:9px;border-right:1px solid rgba(255,255,255,.35);height:52px;display:flex;align-items:center;justify-content:flex-end}
.cta strong{font-family:"Roboto Condensed",sans-serif;font-weight:400;font-size:27px;padding-left:9px}
.cta-shadow{position:absolute;left:205px;top:374px;width:220px;height:12px;border-radius:50%;background:radial-gradient(rgba(0,0,0,.35),transparent 70%)}
.gymnast{position:absolute;left:485px;top:12px;width:430px;height:466px;background:radial-gradient(ellipse at 45% 45%,#3a3a3a 0%,#caa48a 30%,rgba(230,200,180,.4) 55%,transparent 72%)}
.hero-side{position:absolute;left:725px;top:160px}
.hero-side .s1{font-size:25px;color:var(--red)}
.hero-side .s2{font-size:40px;color:var(--red);line-height:1.05}
.hero-side .s3{font-size:25px;color:var(--blue);margin-top:12px}

/* steps */
.steps{position:absolute;left:0;top:581px;width:1200px;height:159px;background:linear-gradient(#b11c22,#a0141a);border-top:2px solid #7a1014}
.step{position:absolute;top:0;width:290px;height:159px}
.step+.step{border-left:1px solid rgba(255,255,255,.15)}
.step-num{position:absolute;left:0;top:6px;font-family:"Roboto Condensed",sans-serif;font-size:50px;color:#fff;line-height:1}
.step-title{position:absolute;left:51px;top:22px;font-size:17px;color:#fff}
.step-art{position:absolute;left:0;top:52px;width:115px;height:95px;border-radius:50%;background:radial-gradient(circle,#6f7d8a,#2a3440 60%,transparent 72%)}
.step-art.globe{background:radial-gradient(circle,#5aa2d8,#1b4f7e 60%,transparent 72%)}
.step-art.face{background:radial-gradient(circle,#58a8f0,#1556b8 60%,transparent 72%)}
.step-body{position:absolute;left:128px;top:53px;width:140px;color:#fff}
.step-body h3{font-weight:400;font-size:11px;color:var(--orange)}
.step-body p{font-size:8.5px;line-height:15.5px;margin-top:4px}
.btn-grey{position:absolute;left:183px;top:123px;width:76px;height:20px;border-radius:2px;background:linear-gradient(#7a7a7a,#4d4d4d);color:#fff;font-size:9px;display:flex;align-items:center;justify-content:center}

/* content */
.col{position:absolute;top:757px;width:258px}
.col h2{font-weight:400;font-size:19.5px;color:var(--blue)}
.col p{font-size:9px;line-height:15.5px;color:var(--grey-text);text-align:justify;margin-top:11px}
.col p+p{margin-top:15px}
.post-link{font-size:11px;color:var(--red);display:block;margin-top:10px}
.post+.post{border-top:1px solid #ddd;margin-top:9px}
.post p{margin-top:5px}
.btn-blue{position:absolute;width:76px;height:20px;border-radius:2px;background:linear-gradient(#2e9ae6,#1572b8);color:#fff;font-size:9px;display:flex;align-items:center;justify-content:center}
.video{position:absolute;left:771px;top:789px;width:258px;height:156px;background:radial-gradient(ellipse at 70% 45%,#6a6258,#2d2b29 55%,#111 100%)}
.video-controls{position:absolute;left:0;bottom:0;width:100%;height:12px;background:#1b1b1b;border-top:1px solid #333}

/* footer */
.site-footer{position:absolute;left:0;top:963px;width:1200px;height:127px;background:var(--footer);color:#fff}
.foot-nav{position:absolute;left:172px;top:25px;font-size:9.5px}
.foot-nav span{margin:0 12px}
.copy{position:absolute;left:172px;top:44px;font-size:9.5px}
.follow{position:absolute;left:833px;top:19px;display:flex;align-items:center;gap:8px;font-size:11.5px}
.follow i{width:28px;height:28px;border-radius:50%;background:#e9e9e9;border:2px solid #444}
.foot-rule{position:absolute;left:172px;top:67px;width:857px;border-top:1px solid var(--footer-line)}
.disclaimer{position:absolute;left:0;top:79px;width:1200px;text-align:center;font-size:9px;line-height:16.5px}
</style>
</head>
<body>

<header class="site-header">
  <div class="brand"><span class="brand-mark"></span><span class="brand-name">Routine verdict</span></div>
  <nav class="main-nav">
    <a class="active" href="#">Home</a>
    <a href="#">About us</a>
    <a href="#">How it works</a>
    <a href="#">FAQ</a>
    <a href="#">Sample Critique</a>
    <a href="#">Member area</a>
  </nav>
  <div class="login">Login &#187;</div>
</header>

<section class="hero">
  <div class="gymnast" role="img" aria-label="Photo of a gymnast in a black leotard performing a handstand split"></div>
  <div class="hero-copy cond">
    <div class="l1">Being Judge</div>
    <div class="l2">has never been Easier...</div>
    <div class="l3">Our Judges only give you a numbers</div>
    <div class="l4">We explain there reasons...</div>
    <p>Lorem Ipsum is simply dummy text of the printing and typesetting industry. Lorem Ipsum has been the industry's standard dummy text ever since the 1500s, when an unknown printer took.</p>
  </div>
  <div class="cta"><small>Upload your video<br>&amp; get critiqued!</small><strong>Get Started</strong></div>
  <div class="cta-shadow"></div>
  <div class="hero-side cond">
    <div class="s1">Your personal</div>
    <div class="s2">Gymnastic Judge!</div>
    <div class="s3">Get judge now!</div>
  </div>
</section>

<section class="steps">
  <div class="step" style="left:165px">
    <div class="step-num" style="left:7px">01</div>
    <div class="step-title" style="left:58px">Record your Routine</div>
    <div class="step-art" role="img" aria-label="Illustration of an HD video camcorder"></div>
    <div class="step-body" style="left:135px"><h3>Videotape your gymnastic</h3><p>Lorem Ipsum is simply dummy text of the printing and typesetting indus try. Lorem Ipsum.</p></div>
    <div class="btn-grey" style="left:189px">Click Here &#8250;</div>
  </div>
  <div class="step" style="left:451px">
    <div class="step-num" style="left:20px">02</div>
    <div class="step-title" style="left:77px">Sign up and Upload</div>
    <div class="step-art globe" style="left:20px" role="img" aria-label="Illustration of a globe with an upload arrow"></div>
    <div class="step-body" style="left:131px"><h3>Videotape your gymnastic</h3><p>Lorem Ipsum is simply dummy text of the printing and typesetting indus try. Lorem Ipsum.</p></div>
    <div class="btn-grey" style="left:202px">Click Here &#8250;</div>
  </div>
  <div class="step" style="left:750px">
    <div class="step-num" style="left:13px">03</div>
    <div class="step-title" style="left:70px">Get the why</div>
    <div class="step-art face" style="left:13px" role="img" aria-label="Illustration of a blue cartoon character with a question mark"></div>
    <div class="step-body" style="left:141px"><h3>Videotape your gymnastic</h3><p>Lorem Ipsum is simply dummy text of the printing and typesetting indus try. Lorem Ipsum.</p></div>
    <div class="btn-grey" style="left:194px">Click Here &#8250;</div>
  </div>
</section>

<section class="col" style="left:173px">
  <h2>About Routine verdict</h2>
  <p>Lorem Ipsum is simply dummy text of the printing and typesetting industry. Lorem Ipsum has been the industry's standard dummy text ever since the 1500s, when an unknown</p>
  <p>printer took a galley of type and scrambled it to make a type specimen book. It has survived not only five centuries, but also the leap into electronic typesetting, remaining essentially.</p>
</section>
<div class="btn-blue" style="left:348px;top:916px">Click Here &#8250;</div>

<section class="col" style="left:472px">
  <h2>Recent posts</h2>
  <div class="post"><a class="post-link">Lorem Ipsum is simply dummy text of the printing</a><p>Lorem Ipsum is simply dummy text of the printing and typesetting industry. Lorem Ipsum has been industry's.</p></div>
  <div class="post"><a class="post-link">Lorem Ipsum is simply dummy text of the printing</a><p>Lorem Ipsum is simply dummy text of the printing and typesetting industry. Lorem Ipsum has been industry's.</p></div>
</section>
<div class="btn-blue" style="left:648px;top:917px">Click Here &#8250;</div>

<section class="col" style="left:772px"><h2>How it works</h2></section>
<div class="video" role="img" aria-label="Video player showing a judge explaining how the service works">
  <svg width="258" height="156" viewBox="0 0 258 156">
    <circle cx="125" cy="61" r="22" fill="none" stroke="rgba(255,255,255,.55)" stroke-width="3"/>
    <path d="M118 48 L140 61 L118 74 Z" fill="rgba(255,255,255,.55)"/>
    <text x="125" y="108" text-anchor="middle" font-family="Roboto Condensed, sans-serif" font-weight="700" font-size="20" fill="rgba(255,255,255,.35)">PLAY</text>
  </svg>
  <div class="video-controls"></div>
</div>

<footer class="site-footer">
  <div class="foot-nav">Home<span>|</span>About us<span>|</span>How it works<span>|</span>FAQ<span>|</span>Sample Critique<span>|</span>Member area</div>
  <div class="copy">Copyright 2012 , Routine Verdict. All rights reserved.</div>
  <div class="follow">Follow Us :<i></i><i></i><i></i><i></i></div>
  <div class="foot-rule"></div>
  <div class="disclaimer">The interpretation of gymnastics judging is subjective. Scores can vary from country, state, region, county, town, etc.<br>The use of this site is for recreational purposes. Our judges are certified gymnastics judges, but gymnastics scoring and routine interpretation can vary from judge to judge.</div>
</footer>

</body>
</html>
```